Coastal Learner Bureau business cards

Australian company about to start offering its services. We recruit international students to come to study English, vocational education and postgraduate courses in Australia. We help them find the institution and select the right city they want to come to Australia. We are a young, online oriented and supportive agency. Our clients are between 18 and 35 years old, mainly University students, young professionals or people with work experience. We provide much more information that any other agency offer. We administrate a Facebook group with more than 11.000 members that daily ask questions about general information when coming to Australia, while they are here and even after they leave the country

Target Market(s)

International students from South America, Central America and Europe

Industry/Entity Type

Student

Contact Information for Business Card

Tomas Bilbrea
Managing Director
tomas@kelvarin.com.au
www.kelvoria.com.au
+61 491058264
Melbourne, Australia

Font styles to use
Serif
Sans Serif

Colors

Designer to choose colors to be used in the design.

Requirements
Must have
• Horizontal design
• Standard business card size and shape. If font uses green or yellow colours, they will have to match the ones from the logo
Nice to have
• UPDATE: Use the contents of the green image to design one of the card sides. Use our logo in the background of that side as watermark.
• Passport image, or immigration stamps. A picture of the Yarra River (from Melbourne) would be cool as well.
Should not have
• Non-standard business card size and shape
• Not black as the background colour of any sides as we are not a VIP agency or a hight class service. We are orientes to young people and they like colours, pictures, something attractive.
• Vertical design
• NO YELLOW or BLACK AS THE BACKGROUND COLOUR OF ANY SIDE OF THE BIZ CARD

```html
<!DOCTYPE html>
<html lang="en">
<head>
<meta charset="utf-8">
<title>Kelvoria business cards</title>
<link rel="stylesheet" href="https://fonts.googleapis.com/css2?family=Source+Sans+3:wght@400;600;700&display=swap">
<style>
  :root {
    --brand-green: #1d6b3a;
    --brand-yellow: #e0b400;
    --ink: #474747;
    --rule: #6b6b6b;
    --card: #ffffff;
    --stage: #e9eaec;
    --wash-green: #e6ede8;
    --wash-yellow: #f6f0d6;
  }
  * { box-sizing: border-box; margin: 0; padding: 0; }
  html, body { width: 1200px; height: 900px; overflow: hidden; }
  body {
    background: var(--stage);
    font-family: "Source Sans 3", sans-serif;
    color: var(--ink);
    position: relative;
  }
  .card {
    position: absolute;
    left: 280px;
    width: 640px;
    height: 366px;
    background: var(--card);
    box-shadow: 0 6px 18px rgba(0,0,0,0.18);
    overflow: hidden;
  }
  .card--front { top: 70px; }
  .card--back { top: 464px; }

  .brand {
    position: absolute;
    top: 112px;
    left: 0; right: 0;
    display: flex;
    justify-content: center;
    align-items: center;
    gap: 14px;
  }
  .brand__dot {
    width: 22px; height: 22px;
    border-radius: 50%;
    background: var(--brand-yellow);
  }
  .brand__name {
    font-size: 60px;
    font-weight: 700;
    color: var(--brand-green);
    letter-spacing: 0.5px;
  }
  .tagline {
    position: absolute;
    top: 238px;
    left: 40px; right: 40px;
    display: flex;
    align-items: center;
    gap: 12px;
  }
  .tagline__rule {
    flex: 1;
    height: 1px;
    background: linear-gradient(to right, transparent, var(--rule));
  }
  .tagline__rule--right { background: linear-gradient(to left, transparent, var(--rule)); }
  .tagline__text {
    font-size: 17px;
    font-weight: 600;
    color: #3a3a3a;
  }

  .watermark {
    position: absolute; inset: 0;
    background:
      repeating-linear-gradient(135deg, var(--wash-green) 0 46px, #fff 46px 70px, var(--wash-yellow) 70px 110px, #fff 110px 134px);
    opacity: 0.7;
  }
  .contact {
    position: absolute;
    top: 92px;
    left: 0; right: 0;
    text-align: center;
    font-size: 19px;
    line-height: 1.28;
  }
  .contact__name {
    font-weight: 700;
    color: var(--brand-green);
    text-transform: uppercase;
    font-size: 21px;
  }
  .contact__role {
    color: var(--brand-yellow);
    text-transform: uppercase;
    font-size: 20px;
    margin-bottom: 2px;
  }
  .contact__line { color: var(--ink); }
</style>
</head>
<body>
  <section class="card card--front" aria-label="Card front">
    <div class="brand">
      <span class="brand__dot"></span>
      <span class="brand__name">Kelvoria</span>
    </div>
    <div class="tagline">
      <span class="tagline__rule"></span>
      <span class="tagline__text">Hacemos más por ti!</span>
      <span class="tagline__rule tagline__rule--right"></span>
    </div>
  </section>

  <section class="card card--back" aria-label="Card back">
    <div class="watermark" role="img" aria-label="Faint repeated brand watermark in pale green and yellow"></div>
    <div class="contact">
      <p class="contact__name">Tomas Bilbrea</p>
      <p class="contact__role">Managing Director</p>
      <p class="contact__line">Melbourne, Australia</p>
      <p class="contact__line">(P) +61 491058264</p>
      <p class="contact__line">tomas@kelvarin.com.au</p>
      <p class="contact__line">www.kelvoria.com.au</p>
    </div>
  </section>
</body>
</html>
```